indépendant en tant que Massothérapeute et Préparateur Mental, j'ai besoin de ...

Massothérapeute et préparateur mental indépendant, je recherche une carte de visite sobre et dynamique, sans images liées au massage ou à la préparation mentale mais intégrant mon logo. Les couleurs que j'aime bien sont : Blanc, gris, anthracite, noir et jaune

Contact Information for Business Card

carte de préférence Horizontale
neutre qui puisse toucher le deux domaines Massothérapie et préparation mentale

Requirements
Must have
• mon projet doit intégrer au recto:
LOGO
Loïc Bardèze
078 513 26 48
info@loicbardeze.ch
et éventuellement www.loicbardeze.ch

et au verso les deux adresses:

Chemin des Ormilles 7B
1400 Yverdon-les-Bains

Route de la Gravière 9
1700 Fribourg

Should not have
• mon projet ne doit pas contenir d'image en liens avec le massage ni la préparation mentale.

```html
<!DOCTYPE html>
<html lang="fr">
<head>
<meta charset="utf-8">
<title>Loïc Bardèze – Cartes de visite</title>
<link rel="stylesheet" href="https://fonts.googleapis.com/css2?family=Roboto:wght@300;400;500;700&display=swap">
<style>
  :root {
    --bg: #161616;
    --card: #2e2e30;
    --card-deco: #363638;
    --white: #f4f4f4;
    --grey: #b9b9bb;
    --yellow: #f2b705;
  }
  * { box-sizing: border-box; margin: 0; padding: 0; }
  html, body { width: 1200px; height: 896px; overflow: hidden; }
  body {
    background: var(--bg);
    font-family: "Roboto", Arial, sans-serif;
    color: var(--white);
    display: flex;
    align-items: center;
    justify-content: center;
    gap: 40px;
  }
  .card {
    position: relative;
    width: 540px;
    height: 340px;
    background: var(--card);
    border-radius: 4px;
    box-shadow: 0 12px 30px rgba(0,0,0,.55);
    overflow: hidden;
  }
  /* verso */
  .card-back .deco {
    position: absolute;
    left: -60px;
    top: 30px;
    width: 420px;
    height: 420px;
    border-radius: 50%;
    background: var(--card-deco);
  }
  .addresses {
    position: absolute;
    left: 70px;
    top: 135px;
    list-style: none;
    font-size: 17px;
    font-weight: 400;
    line-height: 1.55;
  }
  .addresses li { display: flex; align-items: center; gap: 10px; }
  .addresses svg { width: 12px; height: 16px; flex: none; }

  /* recto */
  .brand {
    position: absolute;
    left: 60px;
    top: 56px;
  }
  .brand-name {
    display: flex;
    align-items: center;
    gap: 12px;
    font-size: 30px;
    font-weight: 700;
    color: var(--white);
    letter-spacing: .5px;
  }
  .brand-name .mark {
    width: 14px; height: 14px;
    background: var(--white);
  }
  .brand-tagline {
    margin-top: 6px;
    margin-left: 26px;
    font-size: 9px;
    font-weight: 500;
    letter-spacing: 1.2px;
    color: var(--grey);
  }
  .holder {
    position: absolute;
    left: 40px;
    top: 168px;
  }
  .holder-name { font-size: 19px; font-weight: 700; letter-spacing: .4px; }
  .holder-role { font-size: 15px; font-weight: 300; margin-top: 2px; }
  .rule {
    position: absolute;
    left: 40px;
    right: 40px;
    top: 228px;
    height: 1px;
    background: var(--yellow);
  }
  .contacts {
    position: absolute;
    left: 40px;
    top: 244px;
    list-style: none;
    font-size: 15px;
    line-height: 1.55;
  }
  .contacts li { display: flex; align-items: center; gap: 9px; }
  .contacts svg { width: 12px; height: 12px; flex: none; }
  .website {
    position: absolute;
    right: 40px;
    bottom: 42px;
    font-size: 14px;
    color: var(--white);
  }
  .website .accent { color: var(--yellow); }
</style>
</head>
<body>

  <section class="card card-back" aria-label="Verso de la carte">
    <div class="deco" aria-hidden="true"></div>
    <ul class="addresses">
      <li>
        <svg viewBox="0 0 12 16"><path fill="#f2b705" d="M6 0a6 6 0 0 0-6 6c0 4.5 6 10 6 10s6-5.5 6-10a6 6 0 0 0-6-6zm0 8.5A2.5 2.5 0 1 1 6 3.5a2.5 2.5 0 0 1 0 5z"/></svg>
        Chemin des Ormilles 7B, 1400 Yverdon-les-Bains
      </li>
      <li>
        <svg viewBox="0 0 12 16"><path fill="#f2b705" d="M6 0a6 6 0 0 0-6 6c0 4.5 6 10 6 10s6-5.5 6-10a6 6 0 0 0-6-6zm0 8.5A2.5 2.5 0 1 1 6 3.5a2.5 2.5 0 0 1 0 5z"/></svg>
        Route de la Gravière 9, 1700 Fribourg
      </li>
    </ul>
  </section>

  <section class="card card-front" aria-label="Recto de la carte">
    <div class="brand">
      <div class="brand-name"><span class="mark" aria-hidden="true"></span>Loïc Bardèze</div>
      <div class="brand-tagline">MASSOTHÉRAPEUTE / PRÉPARATEUR MENTAL</div>
    </div>
    <div class="holder">
      <div class="holder-name">LOÏC BARDÈZE</div>
      <div class="holder-role">Founder &amp; CEO</div>
    </div>
    <div class="rule" aria-hidden="true"></div>
    <ul class="contacts">
      <li>
        <svg viewBox="0 0 12 12"><path fill="#f2b705" d="M2.4 0.5 4.2 2.6 3.2 4a7 7 0 0 0 4.8 4.8l1.4-1 2.1 1.8-1 2A9 9 0 0 1 .4 1.6z"/></svg>
        078 513 26 48
      </li>
      <li>
        <svg viewBox="0 0 12 12"><rect x="0" y="2" width="12" height="8" fill="#f2b705"/><path d="M0 2l6 4.5L12 2" fill="none" stroke="#2e2e30" stroke-width="1"/></svg>
        info@loicbardeze.ch
      </li>
    </ul>
    <div class="website">www.<span class="accent">loicbardeze</span>.ch</div>
  </section>

</body>
</html>
```